Vellisant - Quality health delivered at your door

Vellisant offers home and Community Based Services for adults who wish to continue live independently in their communities. We increase accessibility to health care, reduce health care delivery gap, reduce mortality and morbidity, reduce health while promoting healthy living in the comfort of our patients communities or homes.

We provide on site services and deliver high quality healthcare at your door. Our experienced physicians coordinate care with our certified nurse practitioners and provide chronic care management, physical therapy, rehabilitation and medications management.

Target Market(s)

Older population living in independent living facilities

Industry/Entity Type

Health Care

Contact Information for Business Card

Vellisant

Number of Pages Required

4 page

Font styles to use
Sans Serif

Colors

Designer to choose colors to be used in the design.

```html
<!DOCTYPE html>
<html lang="en">
<head>
<meta charset="utf-8">
<title>Vellisant – Quality health delivered at your door</title>
<link rel="stylesheet" href="https://fonts.googleapis.com/css2?family=Aleo:wght@300;400&family=Merriweather:wght@300;400&display=swap">
<style>
:root{
  --green:#5f9a1c;
  --green-dark:#4a8012;
  --green-light:#7fb52f;
  --orange:#f39a10;
  --text:#2b2b2b;
  --muted:#9a9a9a;
  --soft:#f8f8f8;
  --line:#e4e4e4;
  --white:#ffffff;
}
*{margin:0;padding:0;box-sizing:border-box}
html,body{width:1200px;height:3147px;overflow:hidden;background:var(--white)}
body{position:relative;font-family:"Merriweather",Georgia,serif;color:var(--text)}
.abs{position:absolute}

/* header */
.brand{left:0;width:1200px;top:34px;text-align:center}
.brand-dot{width:76px;height:76px;border-radius:50%;background:var(--green);margin:0 auto;border:5px solid var(--orange)}
.brand-name{font-family:"Aleo",Georgia,serif;font-size:21px;font-weight:400;color:var(--green-dark);margin-top:8px;letter-spacing:.5px}

.nav{left:0;top:155px;width:1200px;height:76px;background:linear-gradient(#7db52e,#4f8a14)}
.nav-sep{position:absolute;top:0;width:1px;height:76px;background:rgba(255,255,255,.25)}
.nav-item{position:absolute;top:0;height:76px;width:120px;margin-left:-60px;display:flex;align-items:center;justify-content:center;text-align:center;color:var(--white);font-size:10.5px;line-height:1.6}

/* hero */
.hero{left:0;top:231px;width:1200px;height:556px;overflow:hidden;background:linear-gradient(100deg,#d9cbb2 0%,#efe6d6 35%,#c9b59a 60%,#e8dcc6 100%)}
.hero-curve{position:absolute;left:0;bottom:0}
.hero-title{left:0;width:1200px;top:530px;text-align:center;font-family:"Aleo",Georgia,serif;font-size:64px;font-weight:400;color:var(--white)}
.btn{display:flex;align-items:center;justify-content:center;background:var(--orange);color:var(--white);font-family:"Aleo",Georgia,serif;font-size:15px;border-radius:24px}
.hero-btn{left:497px;top:619px;width:206px;height:46px}
.dots{left:0;width:1200px;top:728px;display:flex;justify-content:center;gap:8px}
.dots span{width:11px;height:11px;border-radius:50%;background:var(--white)}

/* sections */
.section-title{left:0;width:1200px;text-align:center;font-family:"Aleo",Georgia,serif;font-weight:400;font-size:44px;color:var(--green)}
.rule{left:548px;width:104px;height:3px;background:var(--orange)}
.intro{left:250px;width:700px;top:988px;text-align:center;font-size:12.5px;line-height:28px;color:var(--text)}
.intro-btn{left:497px;top:1133px;width:206px;height:46px}

.services-bg{left:0;top:1260px;width:1200px;height:1490px}

.card{width:312px}
.card-photo{width:312px;height:206px}
.card-title{font-family:"Aleo",Georgia,serif;font-weight:300;font-size:22px;line-height:28px;color:var(--text);margin-top:62px}
.card-text{font-size:11.5px;line-height:28px;color:var(--muted);margin-top:52px}

.more{left:577px;top:2604px;width:46px;height:46px;border-radius:50%;background:var(--orange);display:flex;align-items:center;justify-content:center}

/* footer */
.foot-head{top:2836px;font-family:"Aleo",Georgia,serif;font-size:15px;color:var(--orange)}
.foot-list{top:2896px;list-style:none;font-size:10px;line-height:22px;color:var(--text)}
.social{left:862px;top:2898px;display:flex;gap:20px}
.social span{width:14px;height:14px;border-radius:50%;background:#333}
.foot-line{left:0;top:3066px;width:1200px;height:1px;background:var(--line)}
.foot-small{top:3094px;font-size:9.5px;color:var(--text)}
.partner{left:925px;top:3082px;width:72px;height:36px;border-radius:4px;background:#2f74b5}
</style>
</head>
<body>

<header>
  <div class="abs brand">
    <div class="brand-dot"></div>
    <div class="brand-name">VELLISANT</div>
  </div>

  <nav class="abs nav">
    <span class="nav-sep" style="left:120px"></span>
    <span class="nav-sep" style="left:204px"></span>
    <span class="nav-sep" style="left:304px"></span>
    <span class="nav-sep" style="left:392px"></span>
    <span class="nav-sep" style="left:503px"></span>
    <span class="nav-sep" style="left:688px"></span>
    <span class="nav-sep" style="left:766px"></span>
    <span class="nav-sep" style="left:898px"></span>
    <span class="nav-sep" style="left:1022px"></span>
    <span class="nav-sep" style="left:1120px"></span>
    <a class="nav-item" style="left:157px">Home</a>
    <a class="nav-item" style="left:254px">Assisted<br>Living</a>
    <a class="nav-item" style="left:348px">Skilled<br>Nursing</a>
    <a class="nav-item" style="left:445px">Independent<br>Living</a>
    <a class="nav-item" style="left:596px;width:170px;margin-left:-85px">Home &amp; Community<br>Based Services</a>
    <a class="nav-item" style="left:727px">Respite<br>Care</a>
    <a class="nav-item" style="left:832px">Rehabilitation</a>
    <a class="nav-item" style="left:960px">Kindra<br>Learning Centre</a>
    <a class="nav-item" style="left:1071px">Kindra<br>Learning</a>
  </nav>
</header>

<section>
  <div class="abs hero" role="img" aria-label="Photo of a smiling older woman walking arm in arm with a caregiver in a bright hallway">
    <svg class="hero-curve" width="1200" height="80" viewBox="0 0 1200 80" preserveAspectRatio="none">
      <path d="M0 0 Q600 120 1200 0 L1200 80 L0 80 Z" fill="#ffffff"/>
    </svg>
  </div>
  <h1 class="abs hero-title">Vellisant</h1>
  <a class="abs btn hero-btn">Get Started Today</a>
  <div class="abs dots"><span></span><span></span><span></span><span></span></div>
</section>

<section>
  <h2 class="abs section-title" style="top:872px">Stay Home</h2>
  <div class="abs rule" style="top:953px"></div>
  <p class="abs intro">Vellisant offers home and Community Based Services for adults who wish to continue to live independently in the comfort of their communities. We provide on site services and deliver high quality healthcare at your door. Our experienced physicians coordinate care with our certified nurse practitioners and provide chronic care management, physical therapy, rehabilitation and medications management.</p>
  <a class="abs btn intro-btn">Read More</a>
</section>

<section>
  <svg class="abs services-bg" width="1200" height="1490" viewBox="0 0 1200 1490" preserveAspectRatio="none">
    <path d="M0 90 Q600 -40 1200 90 L1200 1410 Q600 1530 0 1410 Z" fill="#ececec"/>
    <path d="M0 110 Q600 0 1200 110 L1200 1390 Q600 1500 0 1390 Z" fill="#f8f8f8"/>
  </svg>

  <h2 class="abs section-title" style="top:1394px">Services</h2>
  <div class="abs rule" style="top:1472px"></div>

  <article class="abs card" style="left:109px;top:1552px">
    <div class="card-photo" role="img" aria-label="Photo of a nurse with a clipboard visiting an older couple at home" style="background:linear-gradient(135deg,#e8e2d8,#a59a8a 60%,#4b7fa8)"></div>
    <h3 class="card-title">Comprehensive Primary<br>Care Services</h3>
    <p class="card-text">Sed ut perspiciatis unde omnis iste natus error sit voluptatem accusantium doloremque laudantium, totam rem aperiam, eaque ipsa quae ab illo inventore veritatis et quasi architecto beatae</p>
  </article>
  <article class="abs card" style="left:445px;top:1552px">
    <div class="card-photo" role="img" aria-label="Photo of a caregiver's hands resting on an older woman's hands" style="background:linear-gradient(135deg,#f2f0ec,#c9c4bc 55%,#8a7566)"></div>
    <h3 class="card-title">Coordination Of Speciality<br>Care</h3>
    <p class="card-text">Sed ut perspiciatis unde omnis iste natus error sit voluptatem accusantium doloremque laudantium, totam rem aperiam, eaque ipsa quae ab illo inventore veritatis et quasi architecto beatae</p>
  </article>
  <article class="abs card" style="left:781px;top:1552px">
    <div class="card-photo" role="img" aria-label="Photo of an older man resting on a park bench" style="background:linear-gradient(135deg,#9cbf4a,#c8d98a 45%,#6d5236)"></div>
    <h3 class="card-title">Chronic Disease<br>Management</h3>
    <p class="card-text">Sed ut perspiciatis unde omnis iste natus error sit voluptatem accusantium doloremque laudantium, totam rem aperiam, eaque ipsa quae ab illo inventore veritatis et quasi architecto beatae</p>
  </article>

  <article class="abs card" style="left:109px;top:2100px">
    <div class="card-photo" role="img" aria-label="Photo of a nurse checking an older woman's arm" style="background:linear-gradient(135deg,#d8c8b8,#d98a9a 45%,#3fa7b8)"></div>
    <h3 class="card-title">Transitional<br>Care</h3>
    <p class="card-text">Sed ut perspiciatis unde omnis iste natus error sit voluptatem accusantium doloremque laudantium, totam rem aperiam, eaque ipsa quae ab illo inventore veritatis et quasi architecto beatae</p>
  </article>
  <article class="abs card" style="left:445px;top:2100px">
    <div class="card-photo" role="img" aria-label="Photo of an older person in a wheelchair enjoying a walk in a park" style="background:linear-gradient(135deg,#5e7a2e,#a7b86a 50%,#8a7a68)"></div>
    <h3 class="card-title">Social Services<br>Assessment</h3>
    <p class="card-text">Sed ut perspiciatis unde omnis iste natus error sit voluptatem accusantium doloremque laudantium, totam rem aperiam, eaque ipsa quae ab illo inventore veritatis et quasi architecto beatae</p>
  </article>
  <article class="abs card" style="left:781px;top:2100px">
    <div class="card-photo" role="img" aria-label="Photo of a group of older adults doing seated exercises" style="background:linear-gradient(135deg,#c9a772,#8a6c5a 50%,#4d5a8a)"></div>
    <h3 class="card-title">Physical<br>Therapy</h3>
    <p class="card-text">Sed ut perspiciatis unde omnis iste natus error sit voluptatem accusantium doloremque laudantium, totam rem aperiam, eaque ipsa quae ab illo inventore veritatis et quasi architecto beatae</p>
  </article>

  <a class="abs more" aria-label="Show more services">
    <svg width="20" height="14" viewBox="0 0 20 14"><path d="M3 3 L10 10 L17 3" fill="none" stroke="#ffffff" stroke-width="3.5" stroke-linecap="round" stroke-linejoin="round"/></svg>
  </a>
</section>

<footer>
  <h4 class="abs foot-head" style="left:168px">Quick Links</h4>
  <ul class="abs foot-list" style="left:170px">
    <li>Comprehensive primary care services</li>
    <li>Coordination of speciality care</li>
    <li>Chronic Disease</li>
    <li>Transitional Care</li>
    <li>Social services assessment</li>
  </ul>
  <ul class="abs foot-list" style="left:413px">
    <li>Home health assistance</li>
    <li>Physical therapy</li>
    <li>Mental health</li>
    <li>Dental health</li>
    <li>Transportation</li>
  </ul>
  <h4 class="abs foot-head" style="left:648px">Other Links</h4>
  <ul class="abs foot-list" style="left:648px">
    <li>Terms Of Use</li>
    <li>Privacy Policy</li>
    <li>Help</li>
    <li>Disclaimer</li>
  </ul>
  <h4 class="abs foot-head" style="left:864px">Social Icons</h4>
  <div class="abs social"><span></span><span></span><span></span><span></span><span></span></div>

  <div class="abs foot-line"></div>
  <p class="abs foot-small" style="left:176px">© 2017 Company Name &nbsp;|&nbsp; All Rights Reserved</p>
  <p class="abs foot-small" style="left:812px">Sites Of Operations</p>
  <div class="abs partner" aria-label="Partner badge"></div>
  <p class="abs foot-small" style="left:1152px">CS</p>
</footer>

</body>
</html>
```